Elevating our current Business Card Design

We want to elevate our current business card with a new design to look like a zenith 300 company. We are a premium lubricant distributor (oil and grease).
We need 2 versions, version 1 is as per the uploaded a copy of our current business card with the English version.
For our Chinese version we need to use the front to be English in English and have the back of the card designed exactly like the front for all info to be in Chinese.
The design template needs to be such that we can amend the template with adding different information for each person's card.
The background colour of the card can be changed- we just need to clearly see all information on the card and logos.
The QJR and Ember steady logos cannot have any colour or display changes- only use the logos attached.
All logos need to be included and all information from the attached current card

```html
<!DOCTYPE html>
<html lang="en">
<head>
<meta charset="utf-8">
<title>KVR Business Card – Front and Back</title>
<link href="https://fonts.googleapis.com/css2?family=Montserrat:wght@400;500;700;800&display=swap" rel="stylesheet">
<style>
  :root {
    --stage: #1d1d1d;
    --card-dark: #151515;
    --card-light: #c6c6c8;
    --band: #cbcbcd;
    --red: #e8302a;
    --white: #ffffff;
    --badge-neutral: #8d8d90;
    --green: #174a32;
  }
  * { margin: 0; padding: 0; box-sizing: border-box; }
  html, body { width: 1200px; height: 1059px; overflow: hidden; }
  body {
    background: var(--stage);
    font-family: "Montserrat", sans-serif;
    position: relative;
  }
  .card {
    position: absolute;
    border-radius: 22px;
    overflow: hidden;
  }

  /* Front */
  .card--front { left: 256px; top: 87px; width: 690px; height: 393px; background: var(--card-dark); }
  .front-brand {
    position: absolute; left: 88px; top: 140px;
    display: flex; align-items: center; gap: 12px;
  }
  .front-brand .mark-dot { width: 22px; height: 22px; border-radius: 50%; background: var(--red); }
  .front-brand .brand-name { color: var(--red); font-weight: 800; font-size: 72px; letter-spacing: 2px; line-height: 1; }
  .divider { position: absolute; left: 350px; top: 87px; width: 2px; height: 174px; background: var(--red); }
  .person { position: absolute; left: 376px; top: 80px; }
  .person-name { color: var(--red); font-weight: 800; font-size: 25px; line-height: 1.1; }
  .person-role { color: var(--white); font-weight: 400; font-size: 14.5px; margin-top: 1px; }
  .contacts { list-style: none; position: absolute; left: 376px; top: 141px; }
  .contacts li {
    display: flex; align-items: center; gap: 15px;
    color: var(--white); font-size: 15px; height: 24.5px;
  }
  .contacts svg { width: 17px; height: 17px; fill: var(--red); flex: none; }
  .address {
    position: absolute; left: 0; right: 0; top: 285px;
    text-align: center; color: var(--white); font-size: 15px;
  }
  .partner-band {
    position: absolute; left: 0; right: 0; bottom: 0; height: 70px; background: var(--band);
  }
  .distributor-tag {
    position: absolute; left: 30px; top: 7px; width: 204px; height: 54px;
    border: 2px solid var(--red); background: #efefef;
    transform: skewX(-8deg);
    display: flex; align-items: center; justify-content: center;
  }
  .distributor-tag span {
    transform: skewX(8deg); display: block;
    color: var(--red); font-weight: 500; font-size: 11px; line-height: 1.2; text-transform: uppercase;
  }
  .supplier-tag {
    position: absolute; left: 226px; top: 7px; width: 176px; height: 54px;
    background: var(--red); transform: skewX(-8deg);
    display: flex; align-items: center; justify-content: center;
  }
  .supplier-tag span {
    transform: skewX(8deg); color: var(--white); font-weight: 700; font-size: 12px;
    text-align: center; line-height: 1.25; text-transform: uppercase;
  }
  .cert-placeholder { position: absolute; border-radius: 50%; background: var(--badge-neutral); }
  .card--front .cert-placeholder { left: 444px; top: 7px; width: 56px; height: 56px; }
  .partner-name { position: absolute; color: var(--green); font-weight: 700; line-height: 1.1; text-align: right; }
  .card--front .partner-name { left: 528px; top: 16px; width: 84px; font-size: 16px; }

  /* Back */
  .card--back { left: 252px; top: 545px; width: 709px; height: 402px; background: var(--card-light); }
  .back-brand {
    position: absolute; left: 56px; top: 28px;
    display: flex; align-items: center; gap: 24px;
  }
  .back-brand .mark-dot { width: 60px; height: 60px; border-radius: 50%; background: var(--red); }
  .back-brand .brand-name { color: var(--red); font-weight: 800; font-size: 250px; letter-spacing: 4px; line-height: 1; }
  .card--back .cert-placeholder { left: 36px; top: 278px; width: 98px; height: 98px; }
  .card--back .partner-name { left: 540px; top: 294px; width: 125px; font-size: 22px; }
</style>
</head>
<body>

<section class="card card--front" aria-label="Business card front">
  <div class="front-brand">
    <span class="mark-dot"></span>
    <span class="brand-name">KVR</span>
  </div>
  <div class="divider"></div>
  <div class="person">
    <h1 class="person-name">Maren Solway</h1>
    <p class="person-role">Administraction Executive</p>
  </div>
  <ul class="contacts">
    <li><svg viewBox="0 0 24 24" aria-hidden="true"><path d="M3 9c0-3 4-5 9-5s9 2 9 5v2h-5V9H8v2H3z"/><path d="M6 12h12l2 9H4z"/><circle cx="12" cy="16" r="2.5" fill="#151515"/></svg>1300 472 610</li>
    <li><svg viewBox="0 0 24 24" aria-hidden="true"><path d="M7 1h10a2 2 0 0 1 2 2v18a2 2 0 0 1-2 2H7a2 2 0 0 1-2-2V3a2 2 0 0 1 2-2zm0 3v14h10V4z"/><circle cx="12" cy="20.5" r="1.2"/></svg>+16 421 908 317</li>
    <li><svg viewBox="0 0 24 24" aria-hidden="true"><path d="M7 2h10v5H7z"/><path d="M3 8h18v9h-3v-4H6v4H3z"/><path d="M7 14h10v8H7z"/></svg>+16 8 9270 4453</li>
    <li><svg viewBox="0 0 24 24" aria-hidden="true"><path d="M2 5h20v14H2z"/><path d="M2 5l10 8 10-8" fill="none" stroke="#151515" stroke-width="2"/></svg>maren.solway@kvrsupply.com</li>
    <li><svg viewBox="0 0 24 24" aria-hidden="true"><circle cx="12" cy="12" r="10"/><path d="M7 6c3 1 2 4 5 4s2 4 0 5-1 4-3 4M16 5c-1 3 2 4 4 4" fill="none" stroke="#151515" stroke-width="1.6"/></svg>www.kvrsupply.com</li>
  </ul>
  <p class="address">48 Freightway Drive Halden, WA 6190</p>

  <div class="partner-band">
    <div class="distributor-tag"><span>Kestrel Valve<br>Resources</span></div>
    <div class="supplier-tag"><span>Tarlow<br>Premium Lubricants</span></div>
    <div class="cert-placeholder" role="img" aria-label="QJR certification badge"></div>
    <p class="partner-name">Ember steady</p>
  </div>
</section>

<section class="card card--back" aria-label="Business card back">
  <div class="back-brand">
    <span class="mark-dot"></span>
    <span class="brand-name">KVR</span>
  </div>
  <div class="cert-placeholder" role="img" aria-label="QJR certification badge"></div>
  <p class="partner-name">Ember steady</p>
</section>

</body>
</html>
```